Anti Cellulite Treatment Massage Oil see link https://www.shoplarix.com/Anti-Cellulite-Treatment-Massa

i need a packaging design for Anti Cellulite Treatment Massage Oil like this
https://www.shoplarix.com/s/ref=nb_sb_noss?url=search-alias%3Daps&field-keywords=Anti+Cellulite+Treatment+Massage+Oil+

our company is kalo see link below https://www.shoplarix.com/Kal%C3%B6-Beauty-Garcinia-Cambogia-Extract/dp/Q72M9XR5T1/ref=sr_1_1_a_it?ie=UTF8&qid=1494884000&sr=8-1&keywords=kalo

its a 8oz / 240 ml

Target Market(s)

health & beauty

Industry/Entity Type

Massage

Font styles to use
Serif
Sans Serif
Decorative
Script

Colors

Designer to choose colors to be used in the design.

Requirements
Must have
• our logo and pump like this seller
• https://www.shoplarix.com/Anti-Cellulite-Treatment-Massage-Oil/dp/Q58K2TW7H4/ref=sr_1_1_a_it?ie=UTF8&qid=1494884194&sr=8-1&keywords=+Anti+Cellulite+Treatment+Massage+Oil
Nice to have
• the most similar to this or even better idea from this link
Should not have
• pictures on the label

```html
<!DOCTYPE html>
<html lang="en">
<head>
<meta charset="utf-8">
<title>kalo Anti Cellulite Massage Oil – Label</title>
<link rel="stylesheet" href="https://fonts.googleapis.com/css2?family=Poppins:wght@300;500;600;700&family=Barlow:wght@500;600&display=swap">
<style>
  :root {
    --canvas: #ffffff;
    --label-black: #0d0d0d;
    --gold-light: #e7cf86;
    --gold-mid: #c9a24a;
    --gold-dark: #9c7a2e;
    --ink-dark: #1a1408;
    --white: #ffffff;
  }
  html, body {
    margin: 0;
    padding: 0;
    width: 1200px;
    height: 1200px;
    overflow: hidden;
    background: var(--canvas);
  }
  .canvas {
    position: relative;
    width: 1200px;
    height: 1200px;
    background: var(--canvas);
  }
  .label {
    position: absolute;
    left: 310px;
    top: 50px;
    width: 580px;
    height: 1100px;
    background: var(--label-black);
    color: var(--white);
  }
  .brand-tab {
    position: absolute;
    left: 181px;
    top: 0;
    width: 218px;
    height: 351px;
  }
  .brand-mark {
    position: absolute;
    left: 181px;
    top: 100px;
    width: 218px;
    text-align: center;
  }
  .brand-dot {
    display: block;
    width: 26px;
    height: 26px;
    margin: 0 auto 14px;
    border-radius: 50%;
    background: var(--white);
  }
  .brand-name {
    font-family: "Poppins", sans-serif;
    font-weight: 500;
    font-size: 46px;
    line-height: 1;
    color: var(--white);
    letter-spacing: 1px;
  }
  .product-title {
    position: absolute;
    left: 0;
    top: 488px;
    width: 580px;
    margin: 0;
    text-align: center;
    font-family: "Poppins", sans-serif;
    font-weight: 700;
    font-size: 60px;
    line-height: 1;
    letter-spacing: -0.5px;
  }
  .product-subtitle {
    position: absolute;
    left: 0;
    top: 565px;
    width: 580px;
    margin: 0;
    text-align: center;
    font-family: "Poppins", sans-serif;
    font-weight: 300;
    font-size: 58px;
    line-height: 1;
    letter-spacing: 0.5px;
  }
  .benefits {
    position: absolute;
    left: 12px;
    top: 696px;
    width: 556px;
    height: 80px;
    box-sizing: border-box;
    border: 2px solid var(--gold-mid);
    padding: 6px;
  }
  .benefits-inner {
    height: 100%;
    background: linear-gradient(90deg, var(--gold-dark), var(--gold-light) 45%, var(--gold-mid));
    display: flex;
    align-items: center;
    justify-content: center;
    font-family: "Barlow", sans-serif;
    font-weight: 600;
    font-size: 32px;
    letter-spacing: 3px;
    color: var(--ink-dark);
  }
  .description {
    position: absolute;
    left: 12px;
    top: 838px;
    width: 556px;
    margin: 0;
    font-family: "Barlow", sans-serif;
    font-weight: 500;
    font-size: 28px;
    line-height: 42px;
  }
  .description span {
    display: block;
    text-align: justify;
    text-align-last: justify;
  }
  .volume {
    position: absolute;
    left: 0;
    top: 1062px;
    width: 580px;
    margin: 0;
    text-align: center;
    font-family: "Poppins", sans-serif;
    font-weight: 600;
    font-size: 32px;
    letter-spacing: 1px;
    line-height: 1;
  }
</style>
</head>
<body>
<main class="canvas">
  <section class="label">
    <svg class="brand-tab" viewBox="0 0 218 351" aria-hidden="true">
      <defs>
        <linearGradient id="tabGold" x1="0" y1="0" x2="1" y2="1">
          <stop offset="0" stop-color="#e7cf86"/>
          <stop offset="0.55" stop-color="#c9a24a"/>
          <stop offset="1" stop-color="#9c7a2e"/>
        </linearGradient>
      </defs>
      <path d="M0 0 H218 V351 C178 351 138 332 109 296 C80 332 40 351 0 351 Z" fill="url(#tabGold)"/>
    </svg>
    <div class="brand-mark">
      <span class="brand-dot"></span>
      <span class="brand-name">kalo</span>
    </div>

    <h1 class="product-title">ANTI CELLULITE</h1>
    <h2 class="product-subtitle">MASSAGE OIL</h2>

    <div class="benefits">
      <div class="benefits-inner">FIRMS · SMOOTHES · TONES</div>
    </div>

    <p class="description">
      <span>Aromatic massage oil targets stubborn</span>
      <span>cellulite in problem are as such as hips,</span>
      <span>thighs, buttocks and abdomen, penetrates</span>
      <span>skin and tackles unwanted fat cells</span>
    </p>

    <p class="volume">8 FL OZ (240 ML)</p>
  </section>
</main>
</body>
</html>
```